New Business Card Design Project

Use the flyer uploaded and website www.brightoakbuilders.com for inspiration.
List Our Services on Backside of business cards
Marcus Delling
Harborline Builders Inc.
Licensed General Contractors
858-471-6093

Contact Information for Business Card

Use the flyer uploaded and website www.brightoakbuilders.com for inspiration. List Our Services on Backside of business cards Marcus Delling Harborline Builders Inc. Licensed General Contractors 858-471-6093

```html
<!DOCTYPE html>
<html lang="en">
<head>
<meta charset="utf-8">
<title>Harborline Builders – Business Card</title>
<link rel="stylesheet" href="https://fonts.googleapis.com/css2?family=Cormorant+Garamond:wght@500&family=Playfair+Display:wght@800&family=Arimo:wght@400&display=swap">
<style>
  :root {
    --bg: #1b1b1d;
    --card-white: #ffffff;
    --card-dark: #2f2f31;
    --ink: #1e1e20;
    --ink-soft: #7a7a7c;
    --light: #f2f2f2;
    --line: #9a9a9c;
  }
  * { margin: 0; padding: 0; box-sizing: border-box; }
  html, body { width: 1200px; height: 963px; overflow: hidden; }
  body {
    background: var(--bg);
    display: flex;
    flex-direction: column;
    align-items: center;
    justify-content: center;
    gap: 48px;
    font-family: "Arimo", Arial, sans-serif;
  }
  .card {
    position: relative;
    width: 700px;
    height: 400px;
    border-radius: 26px;
    overflow: hidden;
    box-shadow: 0 14px 40px rgba(0,0,0,.5);
  }

  /* Shared brand line */
  .brand {
    position: absolute;
    display: flex; align-items: center; gap: 10px;
    font-family: "Cormorant Garamond", serif;
    font-weight: 500;
    letter-spacing: 2px;
    text-transform: uppercase;
    white-space: nowrap;
  }
  .brand__mark { width: 10px; height: 10px; flex: none; }

  /* Front */
  .card--front { background: var(--card-white); color: var(--ink); }
  .front-swoosh { position: absolute; inset: 0; }
  .brand--front {
    left: 250px; top: 112px;
    font-size: 28px;
    color: var(--ink);
  }
  .brand--front .brand__mark { background: var(--ink); }
  .identity {
    position: absolute;
    left: 40px; top: 190px;
    width: 280px;
    text-align: right;
  }
  .identity__name {
    font-family: "Playfair Display", serif;
    font-weight: 800;
    font-size: 24px;
    letter-spacing: 1px;
    text-transform: uppercase;
    white-space: nowrap;
  }
  .identity__role { font-size: 16px; color: var(--ink-soft); margin-top: 6px; white-space: nowrap; }
  .divider {
    position: absolute; left: 340px; top: 188px;
    width: 1px; height: 76px; background: var(--line);
  }
  .contact {
    position: absolute; left: 360px; top: 196px;
    list-style: none; font-size: 16px; color: var(--ink-soft);
  }
  .contact li { display: flex; align-items: center; gap: 10px; margin-bottom: 14px; white-space: nowrap; }
  .contact svg { width: 16px; height: 16px; stroke: var(--ink); fill: none; stroke-width: 1.6; flex: none; }

  /* Back */
  .card--back { background: var(--card-dark); color: var(--light); }
  .services { position: absolute; left: 46px; top: 40px; }
  .services__title {
    font-family: "Cormorant Garamond", serif;
    font-weight: 500; font-size: 34px; letter-spacing: 2px;
    text-transform: uppercase; margin-bottom: 10px; white-space: nowrap;
  }
  .services__list { list-style: none; font-size: 17px; line-height: 28px; }
  .services__list li { display: flex; align-items: center; gap: 8px; white-space: nowrap; }
  .services__list svg { width: 15px; height: 15px; stroke: var(--light); fill: none; stroke-width: 2; flex: none; }
  .brand--back {
    right: 40px; top: 170px;
    font-size: 22px;
    color: var(--light);
  }
  .brand--back .brand__mark { background: var(--light); width: 9px; height: 9px; }
</style>
</head>
<body>

<section class="card card--front" aria-label="Business card front">
  <svg class="front-swoosh" viewBox="0 0 700 400" preserveAspectRatio="none" aria-hidden="true">
    <path d="M0 250 C 100 340, 360 375, 520 400 L0 400 Z" fill="#2a2a2c"/>
    <path d="M0 262 C 120 345, 360 372, 560 400" fill="none" stroke="#c8c8c8" stroke-width="2"/>
  </svg>

  <div class="brand brand--front"><span class="brand__mark"></span>Harborline Builders</div>

  <div class="identity">
    <h1 class="identity__name">Marcus Delling</h1>
    <p class="identity__role">Licensed General Contractors</p>
  </div>
  <div class="divider"></div>
  <ul class="contact">
    <li>
      <svg viewBox="0 0 16 16"><path d="M3 2 L6 2 L7 5 L5 6.5 C6 9 7 10 9.5 11 L11 9 L14 10 L14 13 C8 14 2 8 3 2 Z"/></svg>
      858-471-6093
    </li>
    <li>
      <svg viewBox="0 0 16 16"><circle cx="8" cy="8" r="6.5"/><ellipse cx="8" cy="8" rx="3" ry="6.5"/><path d="M1.5 8 H14.5 M2.5 5 H13.5 M2.5 11 H13.5"/></svg>
      www.brightoakbuilders.com
    </li>
  </ul>
</section>

<section class="card card--back" aria-label="Business card back">
  <div class="services">
    <h2 class="services__title">Our Services</h2>
    <ul class="services__list">
      <li><svg viewBox="0 0 16 16"><circle cx="8" cy="8" r="6.5"/><path d="M5 8.2 L7.2 10.4 L11 6"/></svg>Remodel: Kitchen &amp; Bath</li>
      <li><svg viewBox="0 0 16 16"><circle cx="8" cy="8" r="6.5"/><path d="M5 8.2 L7.2 10.4 L11 6"/></svg>Painting: Interior &amp; Exterior</li>
      <li><svg viewBox="0 0 16 16"><circle cx="8" cy="8" r="6.5"/><path d="M5 8.2 L7.2 10.4 L11 6"/></svg>Flooring: Carpet, Vinyl, Wood</li>
      <li><svg viewBox="0 0 16 16"><circle cx="8" cy="8" r="6.5"/><path d="M5 8.2 L7.2 10.4 L11 6"/></svg>Window &amp; Door Replacement</li>
      <li><svg viewBox="0 0 16 16"><circle cx="8" cy="8" r="6.5"/><path d="M5 8.2 L7.2 10.4 L11 6"/></svg>Plumbing: Repairs &amp; Upgrades</li>
      <li><svg viewBox="0 0 16 16"><circle cx="8" cy="8" r="6.5"/><path d="M5 8.2 L7.2 10.4 L11 6"/></svg>Energy-Efficient Upgrades</li>
      <li><svg viewBox="0 0 16 16"><circle cx="8" cy="8" r="6.5"/><path d="M5 8.2 L7.2 10.4 L11 6"/></svg>Deck &amp; Patio Construction</li>
      <li><svg viewBox="0 0 16 16"><circle cx="8" cy="8" r="6.5"/><path d="M5 8.2 L7.2 10.4 L11 6"/></svg>Water &amp; Mold Damage</li>
      <li><svg viewBox="0 0 16 16"><circle cx="8" cy="8" r="6.5"/><path d="M5 8.2 L7.2 10.4 L11 6"/></svg>Garage Renovation</li>
    </ul>
  </div>
  <div class="brand brand--back"><span class="brand__mark"></span>Harborline Builders</div>
</section>

</body>
</html>
```